NEW Modern Sleek Business Card for VR Language Startup

Our startup is using VR to lead the next wave of world language education. We need a two-sided business card that introduces the larger organization (Brightloom Language Inc) and our contact info on one side and shows the product, Glimwoorld, on the other side.

Side 1 (contact info)= Brightloom Logo and Contact info (name, title, phone, email)

Side 2 (product)= Glimworld logo, text, and website
Text= Culturally Immersive Language Learning Games
Website= www.glimworld-play.com

Target Market(s)

Education, Technology

Contact Information for Business Card

Contact info will be updated upon approval of the design. For now, put this as a placeholder.

Perry Dunmore
Founder & CEO
pdunmore@quillpost-mail.net
(555)-014-2286

Font styles to use
Other font styles liked:
• Gibson and Century Gothic are the brand fonts

Requirements
Nice to have
• I would love to see cohesion between the design and colors of the two logos. I have attached a few business card designs that I like, so you can get a feel for my preferred style.

```html
<!DOCTYPE html>
<html lang="en">
<head>
<meta charset="utf-8">
<title>Brightloom Language Inc – Business Card</title>
<link rel="stylesheet" href="https://fonts.googleapis.com/css2?family=Montserrat:ital,wght@0,500;0,700;1,700&family=Roboto:wght@400;500&display=swap">
<style>
  :root{
    --backdrop:#b9bebe;
    --paper:#f4f3f1;
    --edge:#1f93b3;
    --ink:#2b2b2b;
    --ink-soft:#555555;
    --name-blue:#2f9be8;
    --title-orange:#f4792b;
    --product-blue:#2a7fd6;
    --rule-blue:#3f55d8;
    --parent-red:#d8453a;
  }
  *{box-sizing:border-box;margin:0;padding:0}
  html,body{width:1200px;height:824px;overflow:hidden}
  body{
    background:var(--backdrop);
    display:flex;align-items:center;justify-content:center;gap:44px;
    font-family:"Roboto",Arial,sans-serif;
  }
  .card{
    position:relative;
    width:520px;height:297px;
    background:var(--paper);
    border-bottom:6px solid var(--edge);
    box-shadow:0 14px 30px rgba(0,0,0,.18);
  }
  /* contact side */
  .contact{
    position:absolute;left:112px;top:118px;
    color:var(--ink-soft);
  }
  .contact__headline{display:flex;align-items:baseline;gap:8px;white-space:nowrap}
  .contact__name{font-size:24px;font-weight:500;color:var(--name-blue)}
  .contact__divider{font-size:16px;color:var(--ink-soft)}
  .contact__title{font-size:16px;color:var(--title-orange)}
  .contact__details{margin-top:6px;font-size:14px;white-space:nowrap}
  .contact__details b{color:var(--ink);font-weight:500}

  /* product side */
  .product{position:absolute;inset:0;font-family:"Montserrat",Arial,sans-serif}
  .brand{
    position:absolute;display:flex;align-items:center;gap:10px;
    font-weight:700;white-space:nowrap;
  }
  .brand__dot{border-radius:50%}
  .brand--product{left:86px;top:96px;font-size:30px;color:var(--product-blue)}
  .brand--product .brand__dot{width:22px;height:22px;background:var(--product-blue)}
  .brand--parent{left:318px;top:104px;font-size:24px;color:var(--ink)}
  .brand--parent .brand__dot{width:18px;height:18px;background:var(--parent-red)}
  .product__tagline{
    position:absolute;left:60px;top:160px;
    font-size:14px;font-weight:700;font-style:italic;color:var(--ink);
    white-space:nowrap;
  }
  .product__rule{position:absolute;left:30px;top:186px}
  .product__site{
    position:absolute;left:0;right:0;top:208px;text-align:center;
    font-size:14px;font-weight:500;color:var(--rule-blue);
  }
</style>
</head>
<body>
  <section class="card card--contact" aria-label="Contact side">
    <div class="contact">
      <div class="contact__headline">
        <span class="contact__name">Perry Dunmore</span>
        <span class="contact__divider">|</span>
        <span class="contact__title">Founder &amp; CEO</span>
      </div>
      <p class="contact__details"><b>P:</b> (555)-014-2286 <b>E:</b> pdunmore@quillpost-mail.net</p>
    </div>
  </section>

  <section class="card card--product" aria-label="Product side">
    <div class="product">
      <div class="brand brand--product"><span class="brand__dot"></span>Glimworld</div>
      <div class="brand brand--parent"><span class="brand__dot"></span>Brightloom</div>
      <p class="product__tagline">Culturally Immersive Language Learning Games</p>
      <svg class="product__rule" width="460" height="60" viewBox="0 0 460 60" aria-hidden="true">
        <defs>
          <linearGradient id="ruleFadeL" x1="0" x2="1">
            <stop offset="0" stop-color="#3f55d8" stop-opacity="0"/>
            <stop offset="1" stop-color="#3f55d8"/>
          </linearGradient>
          <linearGradient id="ruleFadeR" x1="0" x2="1">
            <stop offset="0" stop-color="#3f55d8"/>
            <stop offset="1" stop-color="#3f55d8" stop-opacity="0"/>
          </linearGradient>
        </defs>
        <line x1="0" y1="29" x2="82" y2="29" stroke="url(#ruleFadeL)" stroke-width="1.5"/>
        <circle cx="88" cy="29" r="4.5" fill="none" stroke="#3f55d8" stroke-width="1.5"/>
        <circle cx="372" cy="29" r="4.5" fill="none" stroke="#3f55d8" stroke-width="1.5"/>
        <line x1="378" y1="29" x2="460" y2="29" stroke="url(#ruleFadeR)" stroke-width="1.5"/>
      </svg>
      <p class="product__site">www.glimworld-play.com</p>
    </div>
  </section>
</body>
</html>
```